Property Investment eBook Cover

I am a long established Australian property investment adviser, analyst and consultant who is now in semi-retired mode and have re-branded to reflect a more casual and personal approach to advising my property investor clients. I am writing a 'revised edition' to a book written in partnership with my father 20 years ago and need an eBook Cover for this new edition. The eBook will be uploaded to all the regular Australian providers (Corvex Slate, Pebble Ureader, Navi, Leafmarta)

The 3 key elements in the book cover are:

Title: The Harvest Rule of Land. The word 'Property' should be larger and more prominent. eg "The Wealth Power of" could be 1/3 the size of "Property" - with both justified left

Edition: Sydney 2021. "Sydney 2021" should be the focus and dominant imagery of the eBook cover and more prominent than the Title or Author

Author: Colin Marwick, The Housing Examiner. The word "Author" should not appear. "The Housing Examiner" should appear underneath Colin Marwick and justified to Colin Marwick, therefore a smaller font.

The cover should be simple, but eye-catching. No property images, more of an abstract background, than a background with an image. Our preferred colour palette is more blues/greens. Prefer SerifFonts

Copy of book published 20 years ago attached for reference only

```html
<!DOCTYPE html>
<html lang="en">
<head>
<meta charset="utf-8">
<title>The Harvest Rule of Land — eBook Cover</title>
<link rel="stylesheet" href="https://fonts.googleapis.com/css2?family=Playfair+Display:ital,wght@0,400;0,600;0,700;1,400;1,700&display=swap">
<style>
  :root {
    --page: #f4f5f4;
    --band-green: #447e43;
    --title-green: #3f7b40;
    --ink: #0d0d0d;
    --band-text: #f1f8ee;
    --footer-band: rgba(235, 245, 215, 0.72);
    --wash-teal: #a4e4d0;
    --wash-mint: #b2e8cc;
    --wash-sea: #9fdfc0;
    --wash-lime: #b9e488;
  }
  * { margin: 0; padding: 0; box-sizing: border-box; }
  html, body {
    width: 1200px;
    height: 891px;
    overflow: hidden;
    background: var(--page);
  }
  .cover {
    position: absolute;
    left: 303px;
    top: 35px;
    width: 593px;
    height: 820px;
    border-radius: 2px 10px 10px 2px;
    overflow: hidden;
    font-family: "Playfair Display", serif;
  }
  .cover__wash {
    position: absolute;
    inset: 0;
    display: block;
  }
  .wash-stop--teal { stop-color: var(--wash-teal); }
  .wash-stop--mint { stop-color: var(--wash-mint); }
  .wash-stop--sea { stop-color: var(--wash-sea); }
  .wash-stop--lime { stop-color: var(--wash-lime); }
  .edition-band {
    position: absolute;
    left: 0;
    right: 0;
    top: 39px;
    height: 128px;
    background: var(--band-green);
    color: var(--band-text);
    text-align: center;
  }
  .edition-band__label {
    display: block;
    margin-top: 14px;
    font-size: 15px;
    font-weight: 400;
    letter-spacing: 0.6em;
    padding-left: 0.6em;
    line-height: 18px;
  }
  .edition-band__place {
    display: block;
    margin-top: 4px;
    font-style: italic;
    font-weight: 700;
    font-size: 66px;
    letter-spacing: 0.04em;
    line-height: 80px;
  }
  .title {
    position: absolute;
    left: 118px;
    top: 268px;
    color: var(--ink);
    font-weight: 400;
  }
  .title__lead {
    display: block;
    font-size: 33px;
    font-weight: 400;
    letter-spacing: 0.08em;
    line-height: 44px;
  }
  .title__key {
    display: block;
    margin-top: 6px;
    color: var(--title-green);
    font-size: 100px;
    font-weight: 700;
    letter-spacing: 0.1em;
    line-height: 104px;
  }
  .author-band {
    position: absolute;
    left: 0;
    right: 0;
    top: 718px;
    height: 70px;
    background: var(--footer-band);
    text-align: center;
    color: var(--ink);
  }
  .author-band__inner {
    display: inline-block;
    text-align: left;
    margin-top: 11px;
  }
  .author-band__name {
    display: block;
    font-size: 25px;
    font-weight: 600;
    letter-spacing: 0.08em;
    line-height: 30px;
  }
  .author-band__role {
    display: block;
    font-size: 14px;
    letter-spacing: 0.08em;
    line-height: 18px;
  }
</style>
</head>
<body>
  <main class="cover">
    <svg class="cover__wash" width="593" height="820" viewBox="0 0 593 820" role="img" aria-label="Abstract painted wash in soft teal, mint and lime green">
      <defs>
        <linearGradient id="wash" x1="1" y1="0" x2="0" y2="1">
          <stop offset="0" class="wash-stop--teal"/>
          <stop offset="0.45" class="wash-stop--mint"/>
          <stop offset="0.7" class="wash-stop--sea"/>
          <stop offset="1" class="wash-stop--lime"/>
        </linearGradient>
      </defs>
      <rect width="593" height="820" fill="url(#wash)"/>
    </svg>

    <header class="edition-band">
      <span class="edition-band__label">EDITION</span>
      <span class="edition-band__place">SYDNEY 2021</span>
    </header>

    <h1 class="title">
      <span class="title__lead">THE HARVEST</span>
      <span class="title__lead">RULE OF</span>
      <span class="title__key">LAND</span>
    </h1>

    <footer class="author-band">
      <div class="author-band__inner">
        <span class="author-band__name">COLIN MARWICK</span>
        <span class="author-band__role">THE HOUSING EXAMINER</span>
      </div>
    </footer>
  </main>
</body>
</html>
```